Sierra Lantern Roots Festival Music Conference & Concert Series needs a banner design to welco...

We are looking for a banner to use as a backdrop where people can take pictures and promote the event as they upload to social media. The music conference primarily targets high school students so we are looking for a design that will attract a younger audience. The festival revolves around music appreciation in the US/Mexico border. We like the "Sierra LanternRoots Festival" trumpet logo on the "5th annual" design attached, but we are open to other designs.
Target Market(s)
ages 15-45
Colors
Designer to choose colors to be used in the design.
Look and feel

```html
<!DOCTYPE html>
<html lang="en">
<head>
<meta charset="utf-8">
<title>Sierra Lantern Roots Festival — Banner</title>
<link rel="stylesheet" href="https://fonts.googleapis.com/css2?family=Black+Ops+One&family=Comfortaa:wght@500&family=Oswald:wght@700&display=swap">
<style>
  :root {
    --bg-deep: #1d0b52;
    --bg-violet: #4b128f;
    --bg-glow: #5c18a6;
    --magenta: #e312d6;
    --yellow: #fff200;
    --green: #19f51f;
    --cyan: #2aa8d8;
    --mic-cyan: #7ff0ff;
    --white: #ffffff;
  }
  html, body {
    margin: 0;
    padding: 0;
    overflow: hidden;
    background: var(--bg-deep);
  }
  .banner {
    position: relative;
    width: 1200px;
    height: 600px;
    overflow: hidden;
    background:
      radial-gradient(ellipse 75% 95% at 28% 50%, var(--bg-glow) 0%, var(--bg-violet) 50%, var(--bg-deep) 100%);
  }
  .mic-burst {
    position: absolute;
    left: -120px;
    top: -60px;
    width: 720px;
    height: 720px;
    border-radius: 50%;
    background:
      radial-gradient(circle at 50% 55%,
        #0f2a6e 0%, #0f2a6e 15%,
        var(--mic-cyan) 17%, var(--mic-cyan) 21%,
        #3a7be0 24%,
        #b02ad8 38%,
        rgba(227, 18, 214, 0.55) 52%,
        rgba(75, 18, 143, 0) 70%);
  }
  .sparkles {
    position: absolute;
    inset: 0;
  }
  .title-block {
    position: absolute;
    left: 0;
    top: 0;
    width: 1200px;
    height: 600px;
  }
  .edition {
    font-family: "Oswald", sans-serif;
    font-weight: 700;
    font-size: 25px;
    fill: var(--white);
    letter-spacing: 0.5px;
  }
  .rule { fill: var(--cyan); }
  .name-main {
    font-family: "Black Ops One", sans-serif;
    font-size: 74px;
  }
  .name-sierra { fill: var(--magenta); }
  .name-roots { fill: var(--yellow); }
  .name-festival {
    font-family: "Comfortaa", sans-serif;
    font-weight: 500;
    font-size: 60px;
    fill: var(--green);
  }
  .tagline {
    font-family: "Oswald", sans-serif;
    font-weight: 700;
    font-size: 21px;
    fill: var(--white);
    letter-spacing: 0.6px;
  }
</style>
</head>
<body>
  <main class="banner">
    <div class="mic-burst" role="img" aria-label="Glowing neon microphone with radiating cyan and magenta light rays"></div>

    <svg class="sparkles" width="1200" height="600" viewBox="0 0 1200 600" aria-hidden="true">
      <circle cx="28" cy="60" r="11" fill="var(--magenta)"/>
      <circle cx="1145" cy="42" r="10" fill="var(--mic-cyan)"/>
      <circle cx="1000" cy="552" r="11" fill="var(--magenta)"/>
      <circle cx="603" cy="576" r="10" fill="var(--mic-cyan)"/>
      <circle cx="1132" cy="477" r="4" fill="var(--mic-cyan)"/>
      <circle cx="575" cy="93" r="4" fill="var(--mic-cyan)"/>
      <circle cx="916" cy="66" r="4" fill="var(--magenta)"/>
      <circle cx="440" cy="90" r="4" fill="var(--mic-cyan)"/>
      <circle cx="380" cy="250" r="3" fill="var(--mic-cyan)"/>
      <circle cx="182" cy="88" r="4" fill="var(--magenta)"/>
      <circle cx="462" cy="338" r="4" fill="var(--mic-cyan)"/>
      <circle cx="424" cy="540" r="3" fill="var(--mic-cyan)"/>
      <circle cx="378" cy="440" r="4" fill="var(--magenta)"/>
    </svg>

    <svg class="title-block" width="1200" height="600" viewBox="0 0 1200 600">
      <text class="edition" x="666" y="204">5TH ANNUAL</text>
      <rect class="rule" x="668" y="216" width="470" height="8"/>

      <text class="name-main" x="514" y="318" textLength="622" lengthAdjust="spacingAndGlyphs"><tspan class="name-sierra">Sierra Lantern </tspan><tspan class="name-roots">Roots</tspan></text>

      <rect class="rule" x="515" y="336" width="93" height="8"/>
      <text class="name-festival" x="696" y="382">Festival</text>

      <text class="tagline" x="703" y="420" textLength="422" lengthAdjust="spacingAndGlyphs">MUSIC CONFERENCE &amp; CONCERT SERIES</text>
    </svg>
  </main>
</body>
</html>
```